Belvascotravel.com web design project + logo design

Hi,

We are a Russian online tour operator - sunkettle.com

We are looking to tranmsfer our domain to belvascotravel.com. The website and logo need to be belvascoesque - we are not looking to change our functionality, but we need to make the website much more attracitve to clients, much more wild looking but at the same time remaining a professional travel company.

The main concept of the website should be innovative travel (as belvasco was an innovator). Alternatively, you could go down the artist route and go down the draw / design your own tour road.

On our website the customer is able to combine travel services (hotels, flights, Visa services, and soon chauffeur, car rental etc...) put it into their basket (the basket definitely has to look better than it is at the moment) and pay for it in one go by card.

We are also stressin our customer support with web chat, call centre etc... (call centre number at the top of the page)

We aim to provide an easy user experience, but we need to make it have some more style, so I will be waiting for what you guys can come up with.
Let me know if you have any questions - skype is: mrdolbarin

Industry/Entity Type

It Company

Requirements
Must have
• It is quite a simple task - to take the existing website sunkettle.com and belvascosize it to create belvascotravel.com, the functionality of the website will remain the same and there are not many pages in the website. Homepage, Checkout step1, Checkout step 2 (you can view both of these if you select a service) and the generic pages for T&C''s, Privacy policy etc...

IMPORTANT UPDATE

We are also looking at how the search results will look in the designs, (please do a search on our website for hotel / flight)

```html
<!DOCTYPE html>
<html lang="en">
<head>
<meta charset="utf-8">
<title>Belvasco Travel</title>
<link href="https://fonts.googleapis.com/css2?family=Open+Sans:wght@300;400;600;700&display=swap" rel="stylesheet">
<style>
:root{
  --blue:#1e9ad6;
  --blue-frame:#1a9be0;
  --green:#5a9e32;
  --nav-active:#1f5e3a;
  --ink:#333;
  --muted:#888;
  --page:#f3f3f3;
  --footer:#3d3d3d;
  --footer-deep:#333;
  --heading:#1d4f72;
  --map:#3a7bbf;
}
*{margin:0;padding:0;box-sizing:border-box}
html,body{width:1031px;height:1200px;overflow:hidden;background:var(--page)}
body{font-family:"Open Sans",Arial,sans-serif;color:var(--ink)}
.page{position:absolute;left:0;top:0;width:1200px;height:1396px;transform:scale(0.85917);transform-origin:0 0;background:var(--page)}
.abs{position:absolute}

.header{left:0;top:0;width:1200px;height:128px;background:#fff}
.brand{left:135px;top:44px;display:flex;align-items:center;gap:10px;font-size:24px;font-weight:700;color:var(--blue)}
.brand-dot{width:34px;height:34px;border-radius:50%;background:var(--green)}
.nav{top:81px;left:0;width:1200px;font-size:13px}
.nav a{position:absolute;color:#444;text-decoration:none;white-space:nowrap}
.nav a.active{color:var(--nav-active)}
.nav-marker{left:479px;top:0;width:60px;height:3px;background:var(--blue)}
.nav-marker::after{content:"";position:absolute;left:26px;top:3px;border:4px solid transparent;border-top-color:var(--green)}
.social-top span{position:absolute;top:33px;width:26px;height:26px;border:2px solid #555;border-radius:50%}

.hero{left:0;top:128px;width:1200px;height:524px;background:linear-gradient(180deg,#6a9fd8 0%,#b9d3ea 18%,#5f7d55 24%,#4a7a58 30%,#3fc0d6 40%,#7fd6d8 62%,#b8a68c 80%,#8c7a62 100%)}
.caption{left:121px;top:292px;width:367px;height:128px;background:rgba(40,46,48,.78);color:#fff;padding:18px 18px}
.caption h1{font-size:30px;font-weight:700;letter-spacing:.5px;line-height:36px}
.caption p{font-size:16px;line-height:20px;margin-top:9px}

.search{left:128px;top:580px;width:942px;height:72px;background:var(--blue-frame);padding:10px 12px}
.search-inner{position:relative;width:100%;height:55px;background:#fff}
.field{position:absolute;top:10px;width:151px;height:33px;border:1px solid #ccc;border-radius:3px;background:linear-gradient(#fff,#f1f1f1);font-size:12px;color:#666;padding:8px 10px}
.field::after{content:"";position:absolute;right:9px;top:10px;border:3px solid transparent;border-bottom-color:#aaa;box-shadow:0 7px 0 -0px transparent}
.field::before{content:"";position:absolute;right:9px;top:18px;border:3px solid transparent;border-top-color:#aaa}
.sep{position:absolute;top:0;width:1px;height:55px;background:#e4e4e4}
.search-btn{position:absolute;left:800px;top:9px;width:107px;height:34px;background:var(--green);border-radius:2px;color:#fff;font-weight:700;font-size:13px;text-align:center;line-height:34px}

.section-title{left:140px;top:689px;width:920px;font-size:13px;color:#555;text-align:center}
.section-title::before,.section-title::after{content:"";position:absolute;top:8px;height:1px;background:#d8d8d8}
.section-title::before{left:0;width:398px}
.section-title::after{right:0;width:398px}
.service{top:731px;width:215px;height:150px;background:#fff;box-shadow:0 1px 2px rgba(0,0,0,.08);text-align:center}
.service svg{position:absolute;left:77px;top:12px}
.service h3{position:absolute;top:73px;width:100%;font-size:16px;font-weight:400;color:var(--blue)}
.service .more{position:absolute;top:106px;width:100%;font-size:13px;color:var(--green)}

.divider{left:140px;top:920px;width:920px;height:1px;background:#ddd}
.countries-title{left:139px;top:950px;font-size:22px;font-weight:300;color:var(--heading)}
.col{top:1007px;list-style:none;font-size:13px;line-height:24px}
.col li::before{content:"";display:inline-block;border:3px solid transparent;border-left:4px solid var(--green);margin-right:5px;vertical-align:1px}
.world-map{left:780px;top:988px;width:285px;height:160px;background:var(--map);border-radius:40px 60px 30px 50px;opacity:.9}

.footer{left:0;top:1222px;width:1200px;height:133px;background:var(--footer)}
.notch{left:589px;top:1222px;border:9px solid transparent;border-top:9px solid var(--page)}
.foot-nav{top:1263px;font-size:11px;color:var(--muted)}
.foot-nav span{position:absolute;white-space:nowrap}
.foot-line{top:1286px;height:1px;background:#555}
.foot-info{top:1300px;font-size:11px;color:#999;white-space:nowrap;display:flex;align-items:center;gap:8px}
.stay{left:849px;top:1259px;font-size:11px;color:#aaa}
.foot-icon{top:1299px;width:16px;height:16px;background:#777;border-radius:3px}
.bottom{left:0;top:1355px;width:1200px;height:41px;background:var(--footer-deep);font-size:11px;color:#999}
.bottom span{position:absolute;top:14px}
.bottom i{position:absolute;top:11px;width:1px;height:18px;background:#555}
</style>
</head>
<body>
<div class="page">

  <header class="header abs">
    <div class="brand abs"><span class="brand-dot"></span>belvascotravel.com</div>
    <div class="nav-marker abs"></div>
    <nav class="nav abs">
      <a class="active" style="left:489px">HOME</a>
      <a style="left:572px">DESTINATIONS</a>
      <a style="left:706px">ACTIVITIES</a>
      <a style="left:814px">TRIP STYLES</a>
      <a style="left:931px">RESPONSIBLE TRAVEL</a>
    </nav>
    <div class="social-top">
      <span style="left:926px"></span><span style="left:961px"></span><span style="left:996px"></span><span style="left:1031px"></span>
    </div>
  </header>

  <div class="hero abs" role="img" aria-label="Photo of a turquoise bay with smooth granite rocks, green hills and a bright cloudy sky"></div>
  <div class="caption abs">
    <h1>Travel With Belvasco</h1>
    <p>Lorem Ipsum Dolor Sit amet and typesetting industry and ipsum</p>
  </div>

  <form class="search abs">
    <div class="search-inner">
      <div class="field" style="left:13px">Where to go?</div>
      <div class="sep" style="left:188px"></div>
      <div class="field" style="left:212px">Religion?</div>
      <div class="sep" style="left:385px"></div>
      <div class="field" style="left:411px">Check In</div>
      <div class="sep" style="left:584px"></div>
      <div class="field" style="left:603px">Check In</div>
      <div class="sep" style="left:774px"></div>
      <div class="search-btn">SEARCH</div>
    </div>
  </form>

  <div class="section-title abs">OUR SERVICES</div>

  <div class="service abs" style="left:147px">
    <svg width="60" height="50" viewBox="0 0 60 50"><rect x="3" y="9" width="52" height="36" rx="3" fill="none" stroke="#111" stroke-width="4"/><rect x="3" y="18" width="52" height="7" fill="#111"/></svg>
    <h3>Visa Services</h3><div class="more">READ MORE</div>
  </div>
  <div class="service abs" style="left:378px">
    <svg width="60" height="60" viewBox="0 0 60 60"><path d="M30 2l5 0 2 22 16 0 4 4-4 4-16 0-2 22-5 0-6-22-12 0-3 5-3 0 2-9-2-9 3 0 3 5 12 0z" fill="#111" transform="translate(-4 0)"/></svg>
    <h3>Flight Services</h3><div class="more">READ MORE</div>
  </div>
  <div class="service abs" style="left:609px">
    <svg width="60" height="50" viewBox="0 0 60 50"><g transform="translate(30 27)"><circle r="16" fill="#111"/><g fill="#111"><rect x="-5" y="-22" width="10" height="44"/><rect x="-22" y="-5" width="44" height="10"/><rect x="-5" y="-22" width="10" height="44" transform="rotate(45)"/><rect x="-5" y="-22" width="10" height="44" transform="rotate(-45)"/></g><circle r="7" fill="#fff"/></g></svg>
    <h3>Hotel Services</h3><div class="more">READ MORE</div>
  </div>
  <div class="service abs" style="left:840px">
    <svg width="60" height="55" viewBox="0 0 60 55"><path d="M30 4L52 24 30 36 8 24z" fill="none" stroke="#111" stroke-width="3"/><ellipse cx="27" cy="38" rx="14" ry="5" fill="#111"/><rect x="13" y="38" width="28" height="8" fill="#111"/><ellipse cx="27" cy="46" rx="14" ry="5" fill="#111"/></svg>
    <h3>Other Services</h3><div class="more">READ MORE</div>
  </div>

  <div class="divider abs"></div>
  <h2 class="countries-title abs">Countries</h2>
  <ul class="col abs" style="left:140px"><li>Australia</li><li>America</li><li>England</li><li>Inda</li><li>Newzealand</li><li>South Africa</li></ul>
  <ul class="col abs" style="left:244px;top:1006px"><li>Albania</li><li>Bolivia</li><li>Brazil</li><li>Canada</li></ul>
  <ul class="col abs" style="left:349px;top:1008px"><li>Denmark</li><li>Egypt</li><li>Estonia</li><li>France</li><li>Germany</li><li>Greece</li></ul>
  <ul class="col abs" style="left:460px"><li>India</li><li>Italy</li><li>Japan</li><li>China</li></ul>
  <ul class="col abs" style="left:550px;top:1008px"><li>Liberia</li><li>Malaysia</li><li>Mexico</li><li>Monaco</li><li>Morocco</li><li>Norway</li></ul>
  <ul class="col abs" style="left:662px"><li>Phillipines</li><li>Paraguay</li><li>Portugal</li><li>Qatar</li></ul>
  <div class="world-map abs" role="img" aria-label="Flat blue world map silhouette"></div>

  <footer class="footer abs"></footer>
  <div class="notch abs"></div>
  <div class="foot-nav abs" style="left:0">
    <span style="left:130px">Home</span><span style="left:199px">Destinations</span><span style="left:303px">Activities</span><span style="left:389px">Trip Styles</span><span style="left:481px">Responsible Travel</span>
  </div>
  <div class="foot-line abs" style="left:130px;width:698px"></div>
  <div class="foot-line abs" style="left:849px;width:220px"></div>
  <div class="foot-info abs" style="left:130px">
    <svg width="16" height="14" viewBox="0 0 16 14"><path d="M8 1L1 7h2v6h4V9h2v4h4V7h2z" fill="#888"/></svg>
    <span>Lorem Ipsum is simply dummy text of the printinge</span>
  </div>
  <div class="foot-info abs" style="left:465px">
    <svg width="16" height="16" viewBox="0 0 16 16"><path d="M3 1l3 3-2 2c1 2 3 4 5 5l2-2 3 3-2 3C7 14 2 9 1 3z" fill="#888"/></svg>
    <span>(123) 456-7890</span>
  </div>
  <div class="foot-info abs" style="left:595px">
    <svg width="16" height="12" viewBox="0 0 16 12"><rect x="1" y="1" width="14" height="10" fill="#888"/><path d="M1 1l7 6 7-6" fill="none" stroke="#3d3d3d" stroke-width="1.5"/></svg>
    <span>contact@companyname.com</span>
  </div>
  <div class="stay abs">STAY CONNECTED</div>
  <span class="foot-icon abs" style="left:849px;border-radius:50%"></span>
  <span class="foot-icon abs" style="left:884px"></span>
  <span class="foot-icon abs" style="left:919px;border-radius:50%"></span>
  <span class="foot-icon abs" style="left:955px"></span>
  <span class="foot-icon abs" style="left:989px"></span>
  <span class="foot-icon abs" style="left:1024px"></span>

  <div class="bottom abs">
    <span style="left:130px">Belvasco Travel © 2013</span>
    <i style="left:254px"></i>
    <span style="left:270px">Legal Notice</span>
    <i style="left:353px"></i>
    <span style="left:369px">Terms</span>
  </div>
</div>
</body>
</html>
```